Redesign of business card for Cedar Ridge Mechanical

We are looking for a new design for our business cards for Cedar Ridge Mechanical. We are a plumbing & HVAC construction company, operating on the West Coast of Canada and USA. Logo attached.
Industry/Entity Type
Construction - Plumbing & HVAC
Contact Information for Business Card
Name, address, phone numbers, email, website address
Look and feel
Each slider illustrates characteristics of the customer's brand and the style your logo design should communicate.

```html
<!DOCTYPE html>
<html lang="en">
<head>
<meta charset="utf-8">
<title>Cedar Ridge Mechanical – Business Card</title>
<link rel="stylesheet" href="https://fonts.googleapis.com/css2?family=Poppins:wght@300;400;600&display=swap">
<style>
  :root {
    --page-bg: #1b1b1d;
    --card-bg: #202023;
    --card-edge: #2a2a2e;
    --ink: #ffffff;
    --ink-soft: #d9d9dc;
    --band-shadow: rgba(0, 0, 0, 0.45);
    --pattern-light: #2b2b2f;
    --pattern-dark: #19191b;
  }
  * { box-sizing: border-box; margin: 0; padding: 0; }
  html, body {
    width: 1200px;
    height: 780px;
    overflow: hidden;
    background: var(--page-bg);
    font-family: "Poppins", sans-serif;
    color: var(--ink);
  }
  .card-set {
    width: 1200px;
    height: 780px;
    display: flex;
    align-items: center;
    justify-content: center;
    gap: 48px;
  }
  .card {
    position: relative;
    width: 520px;
    height: 300px;
    background: var(--card-bg);
    border: 1px solid var(--card-edge);
    border-radius: 4px;
    overflow: hidden;
    box-shadow: 0 18px 40px rgba(0, 0, 0, 0.55);
  }

  /* Front */
  .card-front .shadow-band {
    position: absolute;
    left: -40px;
    right: -40px;
    top: 96px;
    height: 110px;
    background: linear-gradient(180deg, rgba(0,0,0,0) 0%, var(--band-shadow) 45%, rgba(0,0,0,0) 100%);
    transform: rotate(-4deg);
  }
  .wordmark {
    display: flex;
    align-items: center;
    gap: 10px;
    font-weight: 600;
    color: var(--ink);
    text-transform: uppercase;
    letter-spacing: 0.06em;
  }
  .wordmark .mark-square {
    flex: none;
    background: var(--ink);
  }
  .card-front .wordmark {
    position: absolute;
    top: 34px;
    left: 40px;
    font-size: 15px;
  }
  .card-front .wordmark .mark-square { width: 14px; height: 14px; }
  .person {
    position: absolute;
    top: 108px;
    left: 40px;
  }
  .person-name {
    font-size: 28px;
    line-height: 1.1;
    font-weight: 300;
  }
  .person-name .first { font-weight: 600; }
  .person-role {
    margin-top: 4px;
    font-size: 14px;
    font-weight: 400;
    color: var(--ink-soft);
  }
  .contact-list {
    position: absolute;
    top: 184px;
    left: 40px;
    list-style: none;
  }
  .contact-list li {
    display: flex;
    align-items: center;
    gap: 10px;
    font-size: 13px;
    font-weight: 300;
    line-height: 1;
    margin-bottom: 8px;
    color: var(--ink-soft);
  }
  .contact-icon {
    width: 16px;
    height: 16px;
    flex: none;
  }

  /* Back */
  .card-back .pattern-field {
    position: absolute;
    inset: 0;
    background: linear-gradient(135deg, var(--pattern-light) 0%, var(--pattern-dark) 100%);
  }
  .card-back .wordmark {
    position: absolute;
    inset: 0;
    justify-content: center;
    font-size: 24px;
    gap: 14px;
  }
  .card-back .wordmark .mark-square { width: 22px; height: 22px; }
</style>
</head>
<body>
<main class="card-set">

  <section class="card card-front" aria-label="Business card front">
    <div class="shadow-band"></div>
    <div class="wordmark"><span class="mark-square"></span>Cedar Ridge Mechanical</div>

    <div class="person">
      <h1 class="person-name"><span class="first">Marta</span> Kovalenko</h1>
      <p class="person-role">Founder &amp; CEO</p>
    </div>

    <ul class="contact-list">
      <li>
        <svg class="contact-icon" viewBox="0 0 16 16" aria-hidden="true">
          <circle cx="8" cy="8" r="8" fill="#ffffff"/>
          <path d="M5.2 4.2l1.3-.3.8 1.9-.9.7c.5 1 1.2 1.8 2.2 2.3l.7-.9 1.9.8-.3 1.3c-3.3.2-6-2.5-5.7-5.8z" fill="#202023"/>
        </svg>
        (604) 555-0182
      </li>
      <li>
        <svg class="contact-icon" viewBox="0 0 16 16" aria-hidden="true">
          <circle cx="8" cy="8" r="8" fill="#ffffff"/>
          <rect x="4" y="5.2" width="8" height="5.6" rx="0.6" fill="none" stroke="#202023" stroke-width="1.1"/>
          <path d="M4.3 5.6L8 8.4l3.7-2.8" fill="none" stroke="#202023" stroke-width="1.1"/>
        </svg>
        info@cedarridgemech.com
      </li>
      <li>
        <svg class="contact-icon" viewBox="0 0 16 16" aria-hidden="true">
          <circle cx="8" cy="8" r="8" fill="#ffffff"/>
          <circle cx="8" cy="8" r="4" fill="none" stroke="#202023" stroke-width="1"/>
          <ellipse cx="8" cy="8" rx="1.8" ry="4" fill="none" stroke="#202023" stroke-width="1"/>
          <path d="M4 8h8" stroke="#202023" stroke-width="1"/>
        </svg>
        www.cedarridgemech.com
      </li>
      <li>
        <svg class="contact-icon" viewBox="0 0 16 16" aria-hidden="true">
          <rect x="0" y="0" width="16" height="16" rx="3" fill="#ffffff"/>
          <path d="M8 3.2a3 3 0 0 1 3 3c0 2.2-3 6-3 6s-3-3.8-3-6a3 3 0 0 1 3-3z" fill="#202023"/>
          <circle cx="8" cy="6.2" r="1.1" fill="#ffffff"/>
        </svg>
        418 Alder Bay Road, Bellingham, WA 98225
      </li>
    </ul>
  </section>

  <section class="card card-back" aria-label="Business card back">
    <div class="pattern-field" role="img" aria-label="Repeating faint company emblem pattern in dark grey tones"></div>
    <div class="wordmark"><span class="mark-square"></span>Cedar Ridge Mechanical</div>
  </section>

</main>
</body>
</html>
```